New stationary design for online film company

We need some new stationary to fit with our new logo. The stationary should be professional, clean and simple.
We need designs for a full set of business stationary.
We need - letterhead, envelopes, invoices, proposals, coverslip/note and cover page

Industry/Entity Type

Business

```html
<!DOCTYPE html>
<html lang="en">
<head>
<meta charset="utf-8">
<title>reelwavetv stationery set</title>
<link rel="stylesheet" href="https://fonts.googleapis.com/css2?family=Montserrat:wght@600&family=Open+Sans:wght@400;600&display=swap">
<style>
  :root {
    --navy: #0e4772;
    --sky: #6aa3c0;
    --faint: #eaeef2;
    --paper: #ffffff;
    --ink: #2b2b2b;
    --backdrop: #6e3b27;
  }
  * { margin: 0; padding: 0; box-sizing: border-box; }
  html, body { width: 1200px; height: 770px; overflow: hidden; background: var(--backdrop); }
  body { position: relative; font-family: "Open Sans", sans-serif; color: var(--ink); }

  .wordmark { font-family: "Montserrat", sans-serif; font-weight: 600; color: var(--navy); letter-spacing: -0.5px; display: flex; align-items: center; gap: 8px; white-space: nowrap; }
  .wordmark .dot { border-radius: 50%; background: var(--navy); display: inline-block; }
  .wordmark.light { color: var(--paper); }
  .wordmark.light .dot { background: var(--paper); }

  .sheet { position: absolute; background: var(--paper); }

  /* Letterhead */
  .letterhead { left: 14px; top: 18px; width: 520px; height: 735px; }
  .letterhead .wordmark { position: absolute; top: 44px; left: 0; right: 0; justify-content: center; font-size: 44px; }
  .letterhead .wordmark .dot { width: 40px; height: 40px; }
  .letterhead .watermark { position: absolute; left: 168px; top: 300px; width: 208px; height: 208px; border-radius: 50%; background: var(--faint); }
  .letterhead .footer-rule { position: absolute; left: 0; right: 0; top: 676px; height: 1px; background: var(--navy); }
  .letterhead .footer-band { position: absolute; left: 0; right: 0; top: 680px; height: 24px; background: var(--navy); color: var(--paper); font-size: 8.5px; display: flex; justify-content: center; align-items: center; gap: 12px; }
  .letterhead .footer-band::after { content: ""; position: absolute; left: 0; right: 0; bottom: -4px; height: 1px; background: var(--navy); }
  .contact { display: inline-flex; align-items: center; gap: 4px; }
  .contact svg { width: 8px; height: 8px; }
  .letterhead .address { position: absolute; top: 714px; left: 0; right: 0; text-align: center; font-size: 8.5px; letter-spacing: 0.6px; }

  /* Business cards */
  .card-front { left: 580px; top: 16px; width: 220px; height: 126px; background: var(--navy); }
  .card-front .wordmark { position: absolute; top: 48px; left: 0; right: 0; justify-content: center; font-size: 20px; }
  .card-front .wordmark .dot { width: 14px; height: 14px; }
  .card-front .url { position: absolute; bottom: 8px; left: 0; right: 0; text-align: center; color: var(--paper); font-size: 5.5px; letter-spacing: 1.4px; }

  .card-back { left: 813px; top: 18px; width: 220px; height: 126px; }
  .card-back .wordmark { position: absolute; left: 20px; top: 52px; font-size: 14px; gap: 4px; }
  .card-back .wordmark .dot { width: 11px; height: 11px; }
  .card-back .divider { position: absolute; left: 120px; top: 14px; width: 1px; height: 70px; background: #b9c4cc; }
  .card-back .person { position: absolute; left: 128px; top: 18px; }
  .card-back .name { font-size: 8px; font-weight: 600; color: var(--navy); }
  .card-back .role { font-size: 6px; color: var(--sky); margin-bottom: 6px; }
  .card-back .line { font-size: 5.5px; display: flex; align-items: center; gap: 3px; line-height: 10px; }
  .card-back .line svg { width: 5px; height: 5px; }
  .card-back .band { position: absolute; left: 0; right: 0; top: 102px; height: 10px; background: var(--navy); color: var(--paper); font-size: 5.5px; letter-spacing: 0.5px; text-align: center; line-height: 10px; }
  .card-back .band::before { content: ""; position: absolute; left: 0; right: 0; top: -3px; height: 1px; background: var(--navy); }

  /* Envelope stack */
  .envelope-stack { position: absolute; left: 0; top: 0; }
  .flap-mark { position: absolute; font-size: 18px; }
  .flap-mark .dot { width: 12px; height: 12px; }
  .flap-mark.on-light { left: 829px; top: 196px; }
  .flap-mark.on-dark { left: 829px; top: 288px; }
  .flap-mark.on-white { left: 817px; top: 404px; font-size: 18px; }

  .envelope-front { left: 578px; top: 474px; width: 598px; height: 268px; }
  .envelope-front .wordmark { position: absolute; left: 30px; top: 24px; font-size: 24px; gap: 6px; }
  .envelope-front .wordmark .dot { width: 22px; height: 22px; }
  .envelope-front .address { position: absolute; left: 31px; top: 70px; font-size: 8.5px; letter-spacing: 0.6px; }
  .envelope-front .watermark { position: absolute; left: 520px; top: 150px; width: 58px; height: 58px; border-radius: 50%; background: var(--faint); }
  .envelope-front .band { position: absolute; left: 0; right: 0; top: 230px; height: 16px; background: var(--navy); color: var(--paper); font-size: 7.5px; letter-spacing: 2px; padding-left: 30px; line-height: 16px; font-weight: 600; }
  .envelope-front .band::before, .envelope-front .band::after { content: ""; position: absolute; left: 0; right: 0; height: 1px; background: var(--navy); }
  .envelope-front .band::before { top: -3px; }
  .envelope-front .band::after { bottom: -4px; }
</style>
</head>
<body>

  <section class="sheet letterhead">
    <div class="wordmark"><span class="dot"></span>reelwavetv</div>
    <div class="watermark" aria-hidden="true"></div>
    <div class="footer-rule"></div>
    <div class="footer-band">
      <span class="contact"><svg viewBox="0 0 10 10"><path d="M2 1l2 2-1 1.5c.6 1.2 1.3 1.9 2.5 2.5L7 6l2 2-1.5 1.5C4.5 9 1 5.5.5 2.5z" fill="#fff"/></svg>555-014-2290</span>
      <span class="contact"><svg viewBox="0 0 10 10"><rect x="0.5" y="2" width="9" height="6" fill="#fff"/><path d="M.5 2l4.5 3.5L9.5 2" stroke="#0e4772" fill="none"/></svg>info@reelwavetv.com</span>
      <span class="contact"><svg viewBox="0 0 10 10"><circle cx="5" cy="5" r="4.2" fill="none" stroke="#fff"/><path d="M1 5h8M5 1c-2 2.5-2 5.5 0 8M5 1c2 2.5 2 5.5 0 8" stroke="#fff" fill="none" stroke-width=".7"/></svg>www.reelwavetv.com</span>
    </div>
    <p class="address">00, Complex Name, street, city 000452</p>
  </section>

  <section class="sheet card-front">
    <div class="wordmark light"><span class="dot"></span>reelwavetv</div>
    <p class="url">www.reelwavetv.com</p>
  </section>

  <section class="sheet card-back">
    <div class="wordmark"><span class="dot"></span>reelwavetv</div>
    <div class="divider"></div>
    <div class="person">
      <p class="name">Your Name</p>
      <p class="role">Designation</p>
      <p class="line"><svg viewBox="0 0 10 10"><circle cx="5" cy="5" r="4.5" fill="none" stroke="#2b2b2b"/></svg>555-014-2290</p>
      <p class="line"><svg viewBox="0 0 10 10"><rect x="2.5" y="0.5" width="5" height="9" fill="#2b2b2b"/></svg>555-014-2290</p>
      <p class="line"><svg viewBox="0 0 10 10"><rect x="0.5" y="2" width="9" height="6" fill="#0e4772"/></svg>info@reelwavetv.com</p>
      <p class="line"><svg viewBox="0 0 10 10"><circle cx="5" cy="5" r="4.5" fill="#0e4772"/></svg>www.reelwavetv.com</p>
    </div>
    <div class="band">00, Complex Name, street, city 000452</div>
  </section>

  <svg class="envelope-stack" width="1200" height="770" viewBox="0 0 1200 770" aria-hidden="true">
    <rect x="579" y="166" width="598" height="90" fill="#fff"/>
    <path d="M579 166H1177L1168 200Q1160 214 1140 218L880 246H878H579H620L606 218Q588 212 584 196Z" fill="#6aa3c0"/>
    <rect x="579" y="246" width="598" height="140" fill="#fff"/>
    <path d="M579 246H1177L1170 276Q1165 292 1140 298L890 350Q878 353 866 350L630 300Q596 292 590 276Z" fill="#0e4772"/>
    <rect x="567.5" y="362.5" width="597" height="267" fill="#fff" stroke="#333" stroke-width="1"/>
    <path d="M567.5 362.5L573 388Q578 406 600 412L856 466Q866 468 876 466L1140 412Q1158 406 1160 388L1164.5 362.5" fill="none" stroke="#333" stroke-width="1"/>
  </svg>
  <div class="wordmark light flap-mark on-light"><span class="dot"></span>reelwavetv</div>
  <div class="wordmark light flap-mark on-dark"><span class="dot"></span>reelwavetv</div>
  <div class="wordmark flap-mark on-white"><span class="dot"></span>reelwavetv</div>

  <section class="sheet envelope-front">
    <div class="wordmark"><span class="dot"></span>reelwavetv</div>
    <p class="address">00, Complex Name, street, city 000452</p>
    <div class="watermark" aria-hidden="true"></div>
    <div class="band">www.reelwavetv.com</div>
  </section>

</body>
</html>
```